Business card for a Exhibition booth fabrication company

Hi. My company would like to change our corporate name card. We are an events and Exhibition stand builder company. We would like our corporate name card to resonate what we do. I need someone to create something unique that relates to the industry that I am in. The graphic designer should be creative to incorporate the elements of my industry and try to blend in well in the design of the card. Our aim is to ensure that we are unique and our card can look different from our competitors.
Updates

Target Market(s)

Marketing and events manager from all companies

Contact Information for Business Card

The business card should have the following details:
Name
Job Title
Email
Website

Colors

Designer to choose colors to be used in the design.

Requirements
Must have
• The card must be look something that is relevant to the service that I am providing. My website is: www.velmora-buildworks.com
• You can see my website to get more information on what service that I am doing
Nice to have
• On the back of my card, I would like to have a globe image with the incorporation of my company logo. This is to indicate that my services can be done in any part of the world.

```html
<!DOCTYPE html>
<html lang="en">
<head>
<meta charset="utf-8">
<title>Velmora Buildworks – Business Card</title>
<link href="https://fonts.googleapis.com/css2?family=Roboto:wght@400;500;700&display=swap" rel="stylesheet">
<style>
  :root {
    --red: #e3202a;
    --grey-text: #5b5c5e;
    --grey-card: #606163;
    --grey-line: #7a7b7d;
    --white: #ffffff;
    --stage: #e9e9ea;
  }
  * { box-sizing: border-box; margin: 0; padding: 0; }
  html, body { width: 1200px; height: 900px; overflow: hidden; }
  body {
    background: var(--stage);
    font-family: "Roboto", Arial, sans-serif;
    position: relative;
  }
  .card {
    position: absolute;
    left: 320px;
    width: 560px;
    height: 320px;
    border-radius: 18px;
    overflow: hidden;
    box-shadow: 0 6px 18px rgba(0,0,0,.18);
  }
  .card-front { top: 60px; background: var(--white); }
  .card-back { top: 500px; background: var(--grey-card); }

  .front-swoosh { position: absolute; inset: 0; }

  .brand {
    position: absolute;
    display: flex;
    align-items: center;
    gap: 10px;
    font-weight: 500;
    letter-spacing: 2px;
    text-transform: uppercase;
  }
  .brand-dot { width: 16px; height: 16px; border-radius: 50%; background: var(--red); }
  .card-front .brand { left: 36px; top: 108px; font-size: 17px; color: var(--grey-text); }
  .card-back .brand {
    left: 0; right: 0; top: 0; bottom: 0;
    justify-content: center;
    font-size: 26px;
    color: var(--white);
  }
  .card-back .brand-dot { width: 22px; height: 22px; }

  .divider {
    position: absolute;
    left: 292px; top: 50px;
    width: 2px; height: 150px;
    background: var(--red);
  }
  .details {
    position: absolute;
    left: 312px; top: 46px;
    color: var(--grey-text);
  }
  .person-name {
    color: var(--red);
    font-weight: 700;
    font-size: 24px;
    letter-spacing: .5px;
    text-transform: uppercase;
    line-height: 1;
  }
  .person-title { font-size: 14px; margin: 4px 0 8px; }
  .address { font-size: 12.5px; line-height: 1.35; margin-bottom: 6px; }
  .contact-list { list-style: none; font-size: 12.5px; line-height: 1.5; }
  .contact-list li { display: flex; align-items: center; gap: 6px; }
  .contact-icon { width: 10px; height: 10px; flex: none; }
</style>
</head>
<body>

<section class="card card-front" aria-label="Business card front">
  <svg class="front-swoosh" viewBox="0 0 560 320" preserveAspectRatio="none" aria-hidden="true">
    <path d="M0,150 C140,250 340,285 560,292 L560,320 L0,320 Z" fill="var(--red)"/>
    <path d="M60,190 C200,255 380,280 560,282" fill="none" stroke="var(--grey-line)" stroke-width="4"/>
    <path d="M0,168 C150,262 350,292 560,300" fill="none" stroke="var(--white)" stroke-width="3"/>
    <path d="M440,300 L560,303 L560,320 L430,320 Z" fill="var(--grey-line)"/>
  </svg>

  <div class="brand"><span class="brand-dot"></span>Velmora Buildworks</div>

  <div class="divider"></div>

  <div class="details">
    <p class="person-name">Daniel Harrow</p>
    <p class="person-title">Director</p>
    <p class="address">P.O. Box 4120 Marlow Lane<br>Eastport - Nerova</p>
    <ul class="contact-list">
      <li>
        <svg class="contact-icon" viewBox="0 0 10 10"><path d="M2,0.5 L4,2.5 L3,4 Q4.5,6 6,7 L7.5,6 L9.5,8 L8,9.5 Q3,9 0.5,2 Z" fill="var(--red)"/></svg>
        +65 81427730
      </li>
      <li>
        <svg class="contact-icon" viewBox="0 0 10 10"><rect x="2.5" y="0.5" width="5" height="9" rx="1" fill="none" stroke="var(--red)" stroke-width="1.2"/><circle cx="5" cy="8" r=".6" fill="var(--red)"/></svg>
        +974 55098214
      </li>
      <li>
        <svg class="contact-icon" viewBox="0 0 10 10"><rect x="0.5" y="2" width="9" height="6" fill="none" stroke="var(--red)" stroke-width="1.2"/><path d="M0.5,2 L5,5.5 L9.5,2" fill="none" stroke="var(--red)" stroke-width="1.2"/></svg>
        info@velmora-buildworks.com
      </li>
      <li>
        <svg class="contact-icon" viewBox="0 0 10 10"><circle cx="5" cy="5" r="4.4" fill="none" stroke="var(--red)" stroke-width="1.1"/><ellipse cx="5" cy="5" rx="2" ry="4.4" fill="none" stroke="var(--red)" stroke-width="1"/><path d="M0.6,5 H9.4" stroke="var(--red)" stroke-width="1"/></svg>
        www.velmora-buildworks.com
      </li>
    </ul>
  </div>
</section>

<section class="card card-back" aria-label="Business card back">
  <div class="brand"><span class="brand-dot"></span>Velmora Buildworks</div>
</section>

</body>
</html>
```